New Technology Company is Launching New Products with a New Website

We want to create a 4-page website in WordPress compatible files to launch our site on HostMeadow. The attached files provide our ideas for Products, Services and About Us pages. We believe the content in those files is about right but the actual design is up to the artist that wants to accept this challenge. Additionally we need a fantastic Home page but we have no idea what that looks like. It obviously needs to lead to the other 3 pages but more importantly it needs to capture the interest of our current and future customers.

Details:
1. Please start off using the text descriptions in the example files. If shorter, longer, different descriptions are needed, just let us know.

2. Please feel free to suggest any photos you can find from free or reasonable stock photo services. Picvault and others like them are reasonable. If you find a perfect image, please send us a link and we will buy a license if its affordable. I have paid ~US$10 per image in the past.

3. I have also uploaded our stationery and logo files. We would like the website design to be consistent with the logo and stationery designs. The stationery designs are all in one file.

We have two logos, and would like to see both of them used on the website. One logo shows the letters KRTV in an outlined shield that is read and blue. That logo is used in the stationery and in our draft website design as a header. The other logo shows flames bouncing off a round shield. Perhaps this logo could be used at the bottom of each page on the website, or some other place where it would be fun and creative without diminishing the seriousness of our underlying science and engineering.

4. We are looking for an artist to have some fun with this and propose something creative. We have lots of boring ideas ourselves so we need YOU to do something else! Thank you so much for considering this challenge!

Target Market(s)

People interested in new, high performance fabrics, including consumers, store owners, garment designers and companies like Wolverock or The Ridge Pelt

Coding

Coded - Design and coding required

Font styles to use
Sans Serif

Colors
f04a51
3277b5

Requirements
Must have
• something unforgetable

```html
<!DOCTYPE html>
<html lang="en">
<head>
<meta charset="utf-8">
<title>KRTV – Products</title>
<link href="https://fonts.googleapis.com/css2?family=Roboto:wght@400;500&family=Open+Sans:wght@400;600&display=swap" rel="stylesheet">
<style>
:root{
  --red:#c4000f;
  --brand-red:#f04a51;
  --blue:#1565b0;
  --brand-blue:#3277b5;
  --deep-blue:#0d4a94;
  --ink:#111;
  --body:#666;
  --white:#fff;
  --chart-blue:#1f6fc1;
}
*{box-sizing:border-box;margin:0;padding:0}
html,body{width:1200px;height:3141px;overflow:hidden;background:var(--white)}
body{position:relative;font-family:"Open Sans",Arial,sans-serif;color:var(--body)}
.abs{position:absolute}
/* header */
.site-header{top:0;left:0;width:1200px;height:96px;background:var(--white);z-index:3}
.brand{left:122px;top:26px;display:flex;align-items:center;gap:10px;font-family:"Roboto",Arial,sans-serif;font-weight:500;font-size:30px;color:var(--red)}
.brand-dot{width:36px;height:36px;border-radius:50%;background:var(--brand-blue)}
.main-nav{top:36px;left:374px;display:flex;gap:52px;font-family:"Roboto",Arial,sans-serif;font-size:17px;font-weight:500;color:var(--ink)}
.main-nav .active{color:var(--red)}
/* hero */
.hero{top:96px;left:0;width:1200px;height:444px;
  background:radial-gradient(ellipse at 85% 25%,#e0621b 0%,#7a2708 25%,transparent 55%),radial-gradient(ellipse at 15% 40%,#6b2308 0%,transparent 45%),#0b0604;
  clip-path:polygon(0 0,100% 0,100% 74%,88% 78%,72% 80%,60% 86%,50% 100%,42% 90%,28% 86%,14% 80%,0 76%)}
.hero-title{top:250px;left:0;width:1200px;text-align:center;font-family:"Roboto",Arial,sans-serif;font-size:46px;font-weight:400;color:var(--white);letter-spacing:1px}
/* shared */
.section-title{font-family:"Roboto",Arial,sans-serif;font-size:34px;line-height:1.3;color:var(--ink);font-weight:400}
.section-text{font-size:17px;line-height:1.38}
.section-text p+p{margin-top:22px}
.on-color .section-title,.on-color .section-text{color:var(--white)}
.photo{position:absolute}
/* section 1 */
.insulation{top:636px;left:126px;width:440px}
.photo-dome{left:643px;top:624px;width:421px;height:197px;background:radial-gradient(ellipse at 50% 40%,#e8d9b0 0%,#b41d1a 35%,#1a0b08 75%)}
.chart-temp{left:640px;top:852px}
/* blue band */
.band-blue{top:1190px;left:0}
.aerogel{top:1288px;left:647px;width:392px}
.aerogel .section-text{font-size:16.5px;line-height:24px}
.photo-hiker{left:157px;top:1294px;width:421px;height:197px;background:linear-gradient(180deg,#7fb3e0 0%,#cfdde8 45%,#6a6d6a 70%,#3c3a36 100%)}
.chart-bars{left:150px;top:1506px}
/* fire */
.fabrics{top:1934px;left:132px;width:456px}
.fabrics .section-text{font-size:14.5px;line-height:24px}
.photo-fire{left:651px;top:1926px;width:421px;height:197px;background:radial-gradient(ellipse at 45% 55%,#ffd54a 0%,#f07a12 30%,#5a2b16 70%,#2b2a2e 100%)}
.chart-cal{left:640px;top:2140px}
/* red band */
.band-red{top:2440px;left:0}
.photo-cyclist{left:174px;top:2565px;width:435px;height:325px;background:linear-gradient(180deg,#4a5a6c 0%,#2e4a62 40%,#1d2b3a 100%)}
.wind-list{left:174px;top:2590px;width:435px;font-family:"Roboto",Arial,sans-serif;font-size:13.5px;color:var(--white)}
.wind-row{position:relative;height:41.5px}
.wind-row span{position:absolute;top:0}
.wind-row .name{left:36px}
.wind-row .time{left:334px}
.wind-row i{position:absolute;left:22px;right:36px;top:24px;height:2px}
.wind-row i::before{content:"";position:absolute;left:-2px;top:-5px;border:6px solid transparent;border-right-color:inherit;border-left:0}
.aero{top:2590px;left:651px;width:430px}
/* footer */
.site-footer{top:2984px;left:0;width:1200px;height:157px}
.foot-nav{top:3039px;left:114px;display:flex;gap:46px;font-family:"Roboto",Arial,sans-serif;font-size:17px;color:var(--ink)}
.copyright{top:3081px;left:114px;font-family:"Roboto",Arial,sans-serif;font-size:15px;color:#444}
.foot-brand{left:760px;top:3028px;display:flex;align-items:center;gap:8px;font-family:"Roboto",Arial,sans-serif;font-weight:500;font-size:22px;color:var(--brand-blue)}
.foot-brand .dot{width:44px;height:44px;border-radius:50%;background:var(--brand-red)}
.social{left:912px;top:3034px;display:flex;gap:8px}
.social span{width:34px;height:34px;border-radius:50%}
.page-num{right:8px;top:3114px;font-size:14px;color:#444;font-family:"Roboto",Arial,sans-serif}
</style>
</head>
<body>

<header class="site-header abs">
  <div class="brand abs"><span class="brand-dot"></span>KRTV</div>
  <nav class="main-nav abs">
    <span>HOME</span><span>ABOUT US</span><span>WHY US</span><span class="active">PRODUCTS</span><span>CONTACT</span>
  </nav>
</header>

<div class="hero abs" role="img" aria-label="Glowing sparks and embers against a dark background"></div>
<h1 class="hero-title abs">PRODUCTS</h1>

<section class="insulation abs">
  <h2 class="section-title">High – Temperature<br>Insulation</h2>
  <div class="section-text" style="margin-top:30px">
    <p>KRTV has been working on aerospace applications of high temperature insulations since the Hypersonic Glider Program was proposed by Harlan Vance.</p>
    <p>Back then we used gold and platinum to block heat. Today we make insulations that are much more affordable, more efficient and more reliable in Thermal Protection Systems.</p>
    <p>If this is what you need, contact us and ask about our Opacified Fibrous Insulation (OFI).</p>
  </div>
</section>
<div class="photo photo-dome" role="img" aria-label="Insulation dome under high-temperature test"></div>
<svg class="chart-temp abs" width="430" height="240" viewBox="0 0 430 240" font-family="Open Sans,Arial,sans-serif" font-size="13" fill="#1f6fc1">
  <line x1="52" y1="10" x2="52" y2="200" stroke="#1f6fc1"/>
  <line x1="52" y1="200" x2="390" y2="200" stroke="#1f6fc1"/>
  <g text-anchor="end"><text x="42" y="34">2.0</text><text x="42" y="75">1.5</text><text x="42" y="116">1.0</text><text x="42" y="157">0.5</text><text x="42" y="204">0.0</text></g>
  <g text-anchor="middle"><text x="66" y="222">500</text><text x="126" y="222">1000</text><text x="188" y="222">1500</text><text x="250" y="222">2000</text><text x="312" y="222">2500</text><text x="374" y="222">3000</text></g>
  <path d="M52 168 C170 150 300 120 396 35" fill="none" stroke="#c4000f" stroke-width="2.5"/>
  <path d="M110 200 C220 196 330 170 420 88" fill="none" stroke="#1f6fc1" stroke-width="2.5"/>
</svg>

<svg class="band-blue abs" width="1200" height="680" viewBox="0 0 1200 680">
  <defs><linearGradient id="blueBand" x1="0" y1="0" x2="0" y2="1"><stop offset="0" stop-color="#1a6fc0"/><stop offset="1" stop-color="#0d4a94"/></linearGradient></defs>
  <polygon points="0,8 560,22 0,30" fill="#c4000f"/>
  <polygon points="0,24 1200,6 1200,640 0,660" fill="url(#blueBand)"/>
  <polygon points="640,650 1200,628 1200,650 820,660" fill="#c4000f"/>
</svg>
<div class="photo photo-hiker" role="img" aria-label="Hiker with backpack overlooking snowy mountains"></div>
<svg class="chart-bars abs" width="440" height="260" viewBox="0 0 440 260" font-family="Open Sans,Arial,sans-serif" font-size="12" fill="#fff">
  <g stroke="#ffffff" stroke-opacity=".25"><line x1="40" y1="24" x2="430" y2="24"/><line x1="40" y1="64" x2="430" y2="64"/><line x1="40" y1="104" x2="430" y2="104"/><line x1="40" y1="144" x2="430" y2="144"/><line x1="40" y1="184" x2="430" y2="184"/></g>
  <line x1="40" y1="224" x2="430" y2="224" stroke="#fff" stroke-opacity=".6"/>
  <g text-anchor="end"><text x="26" y="28">50</text><text x="26" y="68">40</text><text x="26" y="108">30</text><text x="26" y="148">20</text><text x="26" y="188">10</text><text x="26" y="228">0</text></g>
  <rect x="55" y="72" width="34" height="152" fill="#1e88e5"/>
  <rect x="140" y="124" width="34" height="100" fill="#c4000f"/>
  <rect x="225" y="164" width="34" height="60" fill="#7ed321"/>
  <rect x="310" y="48" width="34" height="176" fill="#0c3560"/>
  <rect x="395" y="28" width="34" height="196" fill="#4fc3f7"/>
  <g text-anchor="middle"><text x="72" y="242">Goose</text><text x="72" y="255">Down</text><text x="157" y="242">PET</text><text x="157" y="255">FIBER</text><text x="242" y="242">WOOL</text><text x="242" y="255">FELT</text><text x="327" y="242">AEROGEL</text><text x="327" y="255">INSULATION</text><text x="412" y="242">KRTV</text><text x="412" y="255">FRIA</text></g>
</svg>
<section class="aerogel abs on-color">
  <h2 class="section-title">Aerogel Insulations</h2>
  <div class="section-text" style="margin-top:14px">
    <p>KRTV has developed aerogel insulations that are thin, flexible and more than twice as warm as goose down. Although we developed these insulations for ASTRA to take payloads to Mars, we are very excited about their more earthly applications from cold weather clothing to industrial pipelines.</p>
    <p>If this is what you need, contact us and ask about our Fiber Reinforced Insulation with Aerogel (FRIA).</p>
  </div>
</section>

<section class="fabrics abs">
  <h2 class="section-title">Fire Resistant Fabrics</h2>
  <div class="section-text" style="margin-top:14px">
    <p>KRTV developed fire resistant fabrics and insulation blankets that provide various levels of protection for fire fighters surviving a burn over. The current K2002 fire shelter has saved many lives and prevented many injuries, but the tragic loss of 19 Cedar Ridge Hot Shots in 2013 motivated us to develop better fire shelters for today's wild fires that burn hotter and longer than those of 20 years ago.</p>
    <p>If this is what you need, contact us and ask for the KRTV 1080/7, KRTV S/7 and KRTV MLI fabrics.</p>
  </div>
</section>
<div class="photo photo-fire" role="img" aria-label="Large fire burning at an industrial site"></div>
<svg class="chart-cal abs" width="440" height="240" viewBox="0 0 440 240" font-family="Open Sans,Arial,sans-serif" font-size="11" fill="#1f6fc1">
  <text x="220" y="14" text-anchor="middle" font-size="17" fill="#111">Calorimeter Test Per ISO: 9151:1995</text>
  <line x1="34" y1="30" x2="34" y2="210" stroke="#999"/>
  <line x1="34" y1="210" x2="420" y2="210" stroke="#999"/>
  <g text-anchor="end"><text x="26" y="38">60</text><text x="26" y="66">50</text><text x="26" y="94">40</text><text x="26" y="122">30</text><text x="26" y="150">20</text><text x="26" y="178">10</text><text x="26" y="214">0</text></g>
  <g text-anchor="middle"><text x="40" y="228">0</text><text x="66" y="228">5</text><text x="92" y="228">10</text><text x="118" y="228">15</text><text x="144" y="228">20</text><text x="170" y="228">25</text><text x="196" y="228">30</text><text x="222" y="228">35</text><text x="248" y="228">40</text><text x="274" y="228">45</text><text x="300" y="228">50</text><text x="326" y="228">55</text><text x="352" y="228">60</text><text x="378" y="228">65</text><text x="404" y="228">70</text></g>
  <path d="M40 210 C100 190 150 120 190 34" fill="none" stroke="#d0201a" stroke-width="2"/>
  <path d="M50 210 C120 190 180 120 222 34" fill="none" stroke="#f08a1c" stroke-width="2"/>
  <path d="M60 210 C150 190 220 110 262 34" fill="none" stroke="#2a9a3a" stroke-width="2"/>
  <path d="M70 210 C180 190 270 110 318 34" fill="none" stroke="#1a3aa8" stroke-width="2"/>
</svg>

<svg class="band-red abs" width="1200" height="560" viewBox="0 0 1200 560">
  <polygon points="640,22 1200,0 1200,26 900,24" fill="#1565b0"/>
  <polygon points="0,28 1200,22 1200,530 0,540" fill="#c4000f"/>
  <polygon points="0,530 600,544 0,556" fill="#1565b0"/>
</svg>
<div class="photo photo-cyclist" role="img" aria-label="Cyclist riding a road bike in aerodynamic gear"></div>
<div class="wind-list abs">
  <div class="wind-row"><span class="name">Aero TT Helmet</span><span class="time">67 Sec</span><i style="background:#7e57c2;border-color:#7e57c2"></i></div>
  <div class="wind-row"><span class="name">TT Suit</span><span class="time">134 Sec</span><i style="background:#e53935;border-color:#e53935"></i></div>
  <div class="wind-row"><span class="name">Wind Tunnel Positioning</span><span class="time">56 Sec</span><i style="background:#fbc02d;border-color:#fbc02d"></i></div>
  <div class="wind-row"><span class="name">Aerobars</span><span class="time">122 Sec</span><i style="background:#43a047;border-color:#43a047"></i></div>
  <div class="wind-row"><span class="name">Aero Frame</span><span class="time">17 Sec</span><i style="background:#1e88e5;border-color:#1e88e5"></i></div>
  <div class="wind-row"><span class="name">Shoe Covers</span><span class="time">30 Sec</span><i style="background:#4dd0e1;border-color:#4dd0e1"></i></div>
  <div class="wind-row"><span class="name">Rear Disc</span><span class="time">29 Sec</span></div>
</div>
<section class="aero abs on-color">
  <h2 class="section-title">Aerodynamic Fabrics</h2>
  <div class="section-text" style="margin-top:12px">
    <p>KRTV developed and patented aerodynamic fabrics, and measured the drag reduction on bicycles in a wind tunnel.</p>
    <p>If you need to go faster or reduce energy costs, contact us about our SlipVeil fabric</p>
  </div>
</section>

<footer class="site-footer abs"></footer>
<nav class="foot-nav abs"><span>HOME</span><span>ABOUT US</span><span>WHY US</span><span>PRODUCTS</span><span>CONTACT</span></nav>
<p class="copyright abs">© 2018 Company Name&nbsp; All right reserved</p>
<div class="foot-brand abs"><span class="dot"></span>KRTV</div>
<div class="social abs" aria-label="Social links">
  <span style="background:#3b5998"></span><span style="background:#1da1f2"></span><span style="background:#dd4b39"></span><span style="background:#0077b5"></span>
</div>
<span class="page-num abs">X14</span>

</body>
</html>
```